Business Card Design Project

This is the first time we use our new logo. We need a business card that we can use both on our institutional corporate relationships and also that works for our staff that deals with consumers directly.

VELUNDA is a new company dedicated to empower consumers and to provide them with the best choices for specialized health care using the latest telemedicine technology (medicine at a distance via videoconference).

We want to print this cards in high quality materials and process. We will like designs that allow us to use UV spot varnish and other techniques that will differentiate us.

We are including Two different versions of Color logos. In addition we are including white over black background logos. Those can be used replacing the black for a color.

Please note this is the first time we will be creating any corporate materials with our new logo and colors.

Target Market(s)

34+ consumers of medium high and high socioeconomic levels.

Industry/Entity Type

Health

Requirements
Must have
• Our logo on its original colors
Should not have
• Any other graphical element or design that is not our logo

```html
<!DOCTYPE html>
<html lang="en">
<head>
<meta charset="utf-8">
<title>VELUNDA Business Card</title>
<link href="https://fonts.googleapis.com/css2?family=Open+Sans:wght@400;600;700&display=swap" rel="stylesheet">
<style>
  :root {
    --stage: #e4e5e7;
    --card-front: #ffffff;
    --card-back: #1b75bc;
    --brand-blue: #1b75bc;
    --on-blue: #eef1f5;
    --on-blue-mark: #e3e7ee;
  }
  * { margin: 0; padding: 0; box-sizing: border-box; }
  html, body {
    width: 1200px;
    height: 1164px;
    overflow: hidden;
    background: var(--stage);
    font-family: "Open Sans", Arial, sans-serif;
  }
  .canvas {
    position: relative;
    width: 1200px;
    height: 1164px;
  }
  .card {
    position: absolute;
    top: 107px;
    width: 419px;
    height: 734px;
  }
  .card--front {
    left: 164px;
    background: var(--card-front);
  }
  .card--back {
    left: 617px;
    background: var(--card-back);
    color: var(--on-blue);
  }
  .brand {
    position: absolute;
    left: 0;
    width: 100%;
    display: flex;
    flex-direction: column;
    align-items: center;
  }
  .card--front .brand { top: 250px; }
  .card--back .brand { top: 58px; }
  .brand__dot {
    border-radius: 50%;
  }
  .card--front .brand__dot {
    width: 130px;
    height: 130px;
    background: var(--brand-blue);
  }
  .card--back .brand__dot {
    width: 86px;
    height: 86px;
    background: var(--on-blue-mark);
  }
  .brand__name {
    font-weight: 600;
    letter-spacing: 3px;
    line-height: 1;
  }
  .card--front .brand__name {
    margin-top: 38px;
    font-size: 46px;
    color: var(--brand-blue);
  }
  .card--back .brand__name {
    margin-top: 50px;
    font-size: 44px;
    color: var(--on-blue);
  }
  .person {
    position: absolute;
    left: 48px;
    top: 343px;
  }
  .person__name {
    font-size: 19px;
    font-weight: 700;
    letter-spacing: 0.4px;
  }
  .person__title {
    font-size: 12px;
    margin-top: 4px;
  }
  .contact {
    position: absolute;
    left: 47px;
    top: 448px;
    list-style: none;
    font-size: 17px;
    line-height: 25px;
  }
  .contact li:last-child { margin-left: -5px; }
  .address {
    position: absolute;
    left: 39px;
    top: 576px;
    width: 360px;
    font-size: 16.5px;
    line-height: 24.5px;
    font-style: normal;
  }
</style>
</head>
<body>
<main class="canvas">
  <section class="card card--front" aria-label="Card front">
    <div class="brand">
      <span class="brand__dot" aria-hidden="true"></span>
      <span class="brand__name">VELUNDA</span>
    </div>
  </section>

  <section class="card card--back" aria-label="Card back">
    <div class="brand">
      <span class="brand__dot" aria-hidden="true"></span>
      <span class="brand__name">VELUNDA</span>
    </div>

    <div class="person">
      <p class="person__name">Dorin&nbsp; Maszel</p>
      <p class="person__title">CEO</p>
    </div>

    <ul class="contact">
      <li>P: (000) 000-0000</li>
      <li>F: (000) 000-0000</li>
      <li>E: hello@velunda.com</li>
      <li>W: www.velunda.com</li>
    </ul>

    <address class="address">
      0000 Harlow Ln. Suite 000 Brenmoor,<br>
      TT 00000, 000 Harlow Ln. Suite 000<br>
      Brenmoor, TT 000000
    </address>
  </section>
</main>
</body>
</html>
```